Indoor Air Restoration company needs graphic design for a 6x12 v nose trailer to wrap

We offer mold services, duct cleaning, water damage clean up and odor removal. "We find, fix and prevent mold, odor and allergen problems" is what we want to communicate on this trailer, which is a rolling billboard. We like the blue and orange color themes, as found in our logo. The company name is Brightwater Dwelling Services and the logo is attached below. We'd like to see our message clearly, company name and what we offer. We tend to lean towards white letters on a darker background (blue or orange) but are very open to outside ideas, as we are stuck! Our website is available for reference if that is helpful. www.brightwaterdwell.com The phone number to be printed on truck is 302-517-9046, Happy designing!!

Target Market(s)

Home owners

Industry/Entity Type

Indoor Air Quality, Mold Remediation

Font styles to use
Sans Serif

Colors
0054AA
0677BA
7BADD7
CADEEF
E8F1F8
F0912C
F2A743
F7CA91
FBE8D2
FDF5EE

Requirements
Must have
• our message, company name and phone
Nice to have
• services we offer (mold remediation, duct cleaning, water damage and odor removal
Should not have
• cartoon feel

```html
<!DOCTYPE html>
<html lang="en">
<head>
<meta charset="utf-8">
<title>Brightwater Dwelling Services – Trailer Wrap</title>
<link href="https://fonts.googleapis.com/css2?family=Roboto+Condensed:wght@700&family=Montserrat:wght@700&family=Patrick+Hand&display=swap" rel="stylesheet">
<style>
  :root {
    --navy: #0b0b8c;
    --service-blue: #1515c4;
    --orange: #fbae17;
    --orange-line: #f0912c;
    --highlight: rgba(246, 240, 60, 0.75);
    --ink: #111111;
    --white: #ffffff;
    --photo-light: #eef1f5;
    --photo-warm: #e9d3b8;
    --icon-grey: #b9bcc0;
  }
  * { margin: 0; padding: 0; box-sizing: border-box; }
  html, body { width: 848px; height: 1200px; overflow: hidden; background: var(--white); }
  .canvas { position: relative; width: 848px; height: 1200px; }
  .wrap-panel {
    position: absolute; left: 77px; top: 423px;
    width: 706px; height: 353px;
    border: 1px solid #222; overflow: hidden; background: var(--white);
  }
  .panel-shapes { position: absolute; inset: 0; }
  .brand-mark {
    position: absolute; left: 128px; top: 40px;
    display: flex; align-items: center; gap: 8px;
  }
  .brand-mark .mark-square { width: 26px; height: 26px; background: var(--orange); }
  .brand-mark .mark-name {
    font-family: 'Roboto Condensed', sans-serif; font-weight: 700;
    font-size: 20px; line-height: 1.05; color: var(--white);
  }
  .headline {
    position: absolute; left: 280px; top: 28px; width: 320px;
    text-align: center; color: var(--white);
    font-family: 'Roboto Condensed', sans-serif; font-weight: 700;
    text-transform: uppercase; line-height: 1;
  }
  .headline .line-main { display: block; font-size: 46px; }
  .headline .line-sub { display: block; font-size: 32px; margin-top: 4px; }
  .tagline {
    position: absolute; left: 440px; top: 136px; width: 250px;
    font-family: 'Patrick Hand', sans-serif; font-size: 18px; line-height: 22px;
    color: var(--ink); text-align: center;
  }
  .tagline span { background: var(--highlight); padding: 0 6px; }
  .services-title {
    position: absolute; left: 32px; top: 144px;
    font-family: 'Roboto Condensed', sans-serif; font-weight: 700;
    font-size: 22px; color: var(--service-blue); text-decoration: underline;
  }
  .service {
    position: absolute;
    font-family: 'Roboto Condensed', sans-serif; font-weight: 700;
    font-size: 22px; color: var(--service-blue); white-space: nowrap;
  }
  .service::before { content: "• "; }
  .service span { background: var(--highlight); padding: 0 6px 0 2px; }
  .service.mold { left: 31px; top: 180px; }
  .service.water { left: 257px; top: 178px; }
  .service.duct { left: 84px; top: 222px; }
  .service.odor { left: 272px; top: 222px; }
  .phone {
    position: absolute; left: 24px; top: 297px;
    display: flex; align-items: center; gap: 9px;
  }
  .phone-icon { width: 40px; height: 40px; }
  .phone-number {
    font-family: 'Montserrat', sans-serif; font-weight: 700;
    font-size: 33px; letter-spacing: 1.5px; color: var(--ink);
  }
</style>
</head>
<body>
<div class="canvas">
  <section class="wrap-panel">
    <svg class="panel-shapes" width="706" height="353" viewBox="0 0 706 353">
      <defs>
        <linearGradient id="familyPhotoTone" x1="0" y1="0" x2="1" y2="0">
          <stop offset="0" stop-color="var(--white)" stop-opacity="0"/>
          <stop offset="0.4" stop-color="var(--photo-light)"/>
          <stop offset="1" stop-color="var(--photo-warm)"/>
        </linearGradient>
      </defs>
      <rect x="240" y="128" width="466" height="200" fill="url(#familyPhotoTone)" role="img" aria-label="Photo of a smiling family with children resting on a white sofa"/>
      <path d="M0 0 H706 V137 C620 128 520 122 420 130 C330 138 240 150 178 142 C110 132 50 95 0 56 Z" fill="var(--navy)"/>
      <path d="M0 56 C50 95 110 132 178 142 C240 150 330 138 420 130 C520 122 620 128 706 137" fill="none" stroke="var(--orange-line)" stroke-width="2.5"/>
      <path d="M0 261 C70 280 140 292 240 284 C340 276 440 262 540 266 C610 270 660 296 706 325 V353 H0 Z" fill="var(--orange)"/>
      <path d="M0 261 C70 280 140 292 240 284 C340 276 440 262 540 266 C610 270 660 296 706 325" fill="none" stroke="var(--navy)" stroke-width="2.5"/>
    </svg>

    <div class="brand-mark">
      <div class="mark-square"></div>
      <div class="mark-name">Brightwater<br>Dwelling</div>
    </div>

    <h1 class="headline">
      <span class="line-main">Brightwater</span>
      <span class="line-sub">Dwelling Services</span>
    </h1>

    <p class="tagline"><span>We find, fix and prevent mold,</span><br><span>odor and allergen problems</span></p>

    <h2 class="services-title">Our services:</h2>
    <p class="service mold"><span>Mold Remediation</span></p>
    <p class="service water"><span>Water Damage</span></p>
    <p class="service duct"><span>Duct Cleaning</span></p>
    <p class="service odor"><span>Odor Removal</span></p>

    <div class="phone">
      <svg class="phone-icon" viewBox="0 0 40 40" aria-hidden="true">
        <rect x="1" y="1" width="38" height="38" rx="5" fill="var(--icon-grey)"/>
        <path d="M22 9 C16 10 14 15 14 20 C14 25 16 30 22 31 L23 26 C20 25 19 23 19 20 C19 17 20 15 23 14 Z" fill="#333"/>
      </svg>
      <span class="phone-number">302-517-9046</span>
    </div>
  </section>
</div>
</body>
</html>
```